Business Card for a mobile physiotherapy company

I need a layout for a business card for a mobile physiotherapy company.
Slogan is "Mobile Physiotherapy - Your Road To Recovery"
Phone number is 867-555-0142
Email VardenTherapy@postnest.ca (subject to change with website)
Website www.VardenTherapy.ca
My name and credentials: Luke Varden Luke Varden, BSc(kin), MPT, CAFCI, IMS
Information maybe included: Direct Billing, Services including Physiotherapy, IMS, acupuncture
Maybe include facebook and instagram logos
One side with the logo clean and sharp
Other side with details, try not to look too busy, keep everything concise

```html
<!DOCTYPE html>
<html lang="en">
<head>
<meta charset="utf-8">
<title>Varden Therapy – Business Card</title>
<link rel="stylesheet" href="https://fonts.googleapis.com/css2?family=Open+Sans:wght@400;600&family=Tinos:wght@400;700&display=swap">
<style>
  :root {
    --navy: #2c4a75;
    --forest: #0b5549;
    --paper: #ffffff;
    --ink: #1f1f1f;
    --stage: #2a2a2a;
  }
  * { box-sizing: border-box; margin: 0; padding: 0; }
  html, body { width: 1200px; height: 960px; overflow: hidden; background: var(--stage); }
  .canvas { position: relative; width: 1200px; height: 960px; }

  .card {
    position: absolute; left: 250px; width: 700px; height: 400px;
    background: var(--paper); overflow: hidden;
  }
  .card--back { top: 50px; }
  .card--front { top: 510px; }

  /* back side */
  .brand-mark {
    position: absolute; left: 0; right: 0; top: 130px;
    display: flex; align-items: center; justify-content: center; gap: 20px;
    white-space: nowrap;
  }
  .brand-mark__square { width: 40px; height: 40px; background: var(--navy); flex: none; }
  .brand-mark__name {
    font-family: "Open Sans", sans-serif; font-weight: 600; font-size: 54px;
    color: var(--navy); line-height: 1;
  }
  .socials {
    position: absolute; left: 0; right: 0; top: 285px;
    display: flex; justify-content: center; gap: 70px;
    font-family: "Open Sans", sans-serif; font-size: 21px; color: var(--ink);
  }
  .social { display: flex; align-items: center; gap: 10px; }
  .social__square { width: 24px; height: 24px; background: var(--navy); }

  /* front side */
  .front-bands { position: absolute; inset: 0; }
  .wordmark {
    position: absolute; left: 30px; top: 40px;
    display: flex; align-items: center; gap: 12px; white-space: nowrap;
  }
  .wordmark__square { width: 22px; height: 22px; background: var(--navy); }
  .wordmark__name {
    font-family: "Open Sans", sans-serif; font-weight: 600; font-size: 30px;
    color: var(--navy); line-height: 1;
  }
  .slogan {
    position: absolute; left: 30px; top: 100px;
    font-family: "Tinos", serif; font-size: 19px; color: var(--ink);
  }
  .contact {
    position: absolute; left: 28px; top: 172px; list-style: none;
    font-family: "Open Sans", sans-serif; font-size: 18px; color: var(--paper);
  }
  .contact li { display: flex; align-items: center; gap: 9px; height: 30px; }
  .contact svg { width: 16px; height: 16px; fill: none; stroke: var(--paper); stroke-width: 2; }
  .person { position: absolute; right: 30px; top: 112px; text-align: right; }
  .person__name {
    font-family: "Tinos", serif; font-weight: 700; font-size: 27px;
    letter-spacing: 2px; color: var(--navy);
  }
  .person__creds { font-family: "Open Sans", sans-serif; font-size: 14px; color: var(--ink); }
  .services {
    position: absolute; right: 30px; top: 272px; text-align: right;
    font-family: "Open Sans", sans-serif; color: var(--paper); list-style: none;
  }
  .services__title { font-weight: 600; font-size: 17px; margin-bottom: 4px; }
  .services__item { font-size: 16px; line-height: 20px; }
  .services__item::after { content: " •"; }
</style>
</head>
<body>
<main class="canvas">

  <section class="card card--back" aria-label="Card back">
    <div class="brand-mark">
      <span class="brand-mark__square"></span>
      <span class="brand-mark__name">Varden Therapy</span>
    </div>
    <div class="socials">
      <span class="social"><span class="social__square"></span>VardenTherapy</span>
      <span class="social"><span class="social__square"></span>@VardenTherapy</span>
    </div>
  </section>

  <section class="card card--front" aria-label="Card front">
    <svg class="front-bands" viewBox="0 0 700 400" aria-hidden="true">
      <polygon points="0,150 440,150 300,318 0,318" fill="var(--navy)"/>
      <polygon points="430,250 700,250 700,400 340,400" fill="var(--forest)"/>
    </svg>

    <div class="wordmark">
      <span class="wordmark__square"></span>
      <span class="wordmark__name">Varden Therapy</span>
    </div>
    <p class="slogan">Mobile Physiotherapy - Your Road To Recovery</p>

    <ul class="contact">
      <li>
        <svg viewBox="0 0 16 16"><circle cx="8" cy="8" r="7"/><path d="M5.5 4.5l1.5 1.5-1 1.2a6 6 0 0 0 2.8 2.8l1.2-1 1.5 1.5-1 1.2c-3 0-6-3-6-6z"/></svg>
        867-555-0142
      </li>
      <li>
        <svg viewBox="0 0 16 16"><circle cx="8" cy="8" r="7"/><rect x="4" y="5.5" width="8" height="5"/><path d="M4 5.5l4 3 4-3"/></svg>
        VardenTherapy@postnest.ca
      </li>
      <li>
        <svg viewBox="0 0 16 16"><circle cx="8" cy="8" r="7"/><ellipse cx="8" cy="8" rx="3" ry="7"/><path d="M1 8h14"/></svg>
        www.VardenTherapy.ca
      </li>
    </ul>

    <div class="person">
      <p class="person__name">LUKE VARDEN</p>
      <p class="person__creds">BSc(kin), MPT, CAFCI, IMS</p>
    </div>

    <ul class="services">
      <li class="services__title">Services Including</li>
      <li class="services__item">Physiotherapy</li>
      <li class="services__item">Direct Billing</li>
      <li class="services__item">Ims</li>
      <li class="services__item">Acupuncture</li>
    </ul>
  </section>

</main>
</body>
</html>
```